Bring me business with this creative business card

Design my new business card. I am looking for something different with an impact. People will take a look at this card & they will 1- see how different & creative I am, 2-understand what I do 3- Call me to meet me!

I make videos with a message, testimonials. I am dynamic, fun, creative & human. My new website is in construction but in the meantime you can check this old one: brightpath.ca & another one Tidebloom.com & tidebloom facebook page.
I make videos. sometimes with a cameraman, sometimes with my phone. As an ex Public Relations agent, the message is the most important thing for me. I want to make my clients shine! When they start with me they often remind me of a lamb, when I finish coaching them they are powerful like LIONS! That's why I need a powerful business card!

Target Market(s)

Entrepreneurs, solo entrepreneurs, small & medium companies & start ups. People i will meet while networking. People that need videos on their website & social Networks to get attention, to be visible. men & women. From 35 to 49 years old.
I am an ex Public relations agent. I used to send clients in traditional medias, now with videos they have more chances to be seen on google the new media. I do videos of the president, his team, his loyal clients saying how great the company is & expert videos like series so people can be seen for example every 1 st of every month with a short 2 minute video. Also with my 20 years in marketing & communications I can coach & give tips to anybody who needs it.
Target: anybody who would like my old website brightpath.ca & I also have another website but it will be off line soon: tidebloom.com could give you ideas.

Industry/Entity Type

Communications

Contact Information for Business Card

I am in Montreal,So the business cards have to be the usual size like we have in Montreal: 9 cm x 5 cm
Details:My text: Mathilde Tessier MESSAGE COACH/HEAD STORYTELLER. "Making Stories as bold as you are" off: 514-555-0147 cell: 514-555-0183. tidebloom.com
mathilde@tidebloom.com logo facebook, youtube, instagram

Colors
f37122

Requirements
Must have
• Dynamic, happy. Orange. Be creative in the look but NOT the shape of the card. Easy to read. Big enough to read.
Should not have
• No funny shapes: no round, no square, just the usual. I love creative but NOT on shape.

```html
<!DOCTYPE html>
<html lang="en">
<head>
<meta charset="utf-8">
<title>Tidebloom business card</title>
<link href="https://fonts.googleapis.com/css2?family=Roboto:wght@400;500;700&family=Roboto+Condensed:wght@400&display=swap" rel="stylesheet">
<style>
  :root {
    --backdrop: #2a2b2d;
    --card-dark: #1f2022;
    --card-light: #f6f6f6;
    --orange: #f37122;
    --orange-deep: #ec5a24;
    --amber: #f7a823;
    --ink: #4a4a4a;
    --rule-light: #9a9a9a;
    --rule-dark: #e8e8e8;
  }
  * { margin: 0; padding: 0; box-sizing: border-box; }
  html, body { width: 1200px; height: 960px; overflow: hidden; }
  body {
    background: var(--backdrop);
    font-family: "Roboto", Arial, sans-serif;
    position: relative;
  }
  .card { position: absolute; width: 600px; height: 342px; }

  /* Front */
  .card--front { left: 322px; top: 108px; background: var(--card-dark); }
  .front-mark {
    position: absolute; left: 255px; top: 62px;
    width: 90px; height: 90px; border-radius: 50%;
    background: var(--orange);
  }
  .brand-name {
    position: absolute; left: 0; width: 100%; text-align: center;
    font-family: "Roboto", Arial, sans-serif; font-weight: 500;
    color: var(--orange); letter-spacing: 2px; white-space: nowrap;
  }
  .card--front .brand-name { top: 196px; font-size: 36px; }
  .tagline {
    position: absolute; left: 0; width: 100%;
    display: flex; justify-content: center; align-items: center; gap: 6px;
    font-family: "Roboto Condensed", Arial, sans-serif; color: var(--amber);
    white-space: nowrap;
  }
  .tagline::before, .tagline::after {
    content: ""; display: block; height: 1.5px; background: var(--amber);
  }
  .card--front .tagline { top: 236px; font-size: 14px; }
  .card--front .tagline::before, .card--front .tagline::after { width: 30px; }
  .slogan {
    position: absolute; left: 0; top: 255px; width: 100%; text-align: center;
    font-size: 14px; font-weight: 500; color: var(--orange);
  }
  .social-row {
    position: absolute; left: 166px; top: 296px; width: 270px;
    display: flex; align-items: center; gap: 4px;
  }
  .social-row .rule { flex: 1; height: 1px; background: linear-gradient(90deg, var(--rule-dark), var(--orange)); }
  .social-row .rule:last-child { background: linear-gradient(90deg, var(--orange), var(--rule-dark)); }
  .social-dot { width: 23px; height: 23px; border-radius: 50%; background: var(--orange-deep); }

  /* Back */
  .card--back { left: 320px; top: 493px; background: var(--card-light); }
  .back-mark {
    position: absolute; left: 442px; top: 30px;
    width: 80px; height: 80px; border-radius: 50%;
    background: var(--orange);
  }
  .card--back .brand-name {
    left: 388px; width: 190px; top: 136px; font-size: 30px; letter-spacing: 1px;
  }
  .card--back .tagline { left: 388px; width: 190px; top: 168px; font-size: 11px; gap: 5px; }
  .card--back .tagline::before, .card--back .tagline::after { width: 22px; }
  .person-name {
    position: absolute; left: 32px; top: 195px;
    font-size: 22px; font-weight: 700; color: var(--orange-deep);
  }
  .person-role {
    position: absolute; left: 32px; top: 222px;
    font-size: 15px; font-weight: 500; color: var(--amber);
  }
  .divider { position: absolute; left: 32px; top: 249px; width: 536px; height: 1px; background: var(--rule-light); }
  .contact-list { position: absolute; left: 32px; top: 260px; list-style: none; }
  .contact-list li {
    display: flex; align-items: center; gap: 9px;
    font-size: 14px; color: var(--ink); height: 19.5px;
  }
  .contact-list svg { width: 12px; height: 12px; fill: var(--orange-deep); }
  .website { position: absolute; right: 30px; top: 300px; font-size: 14px; color: var(--ink); }
</style>
</head>
<body>
  <section class="card card--front" aria-label="Card front">
    <div class="front-mark" aria-hidden="true"></div>
    <div class="brand-name">TIDEBLOOM</div>
    <div class="tagline">1 STORY &nbsp;1 PURPOSE</div>
    <p class="slogan">Making Stories as bold as you are</p>
    <div class="social-row">
      <span class="rule"></span>
      <span class="social-dot" aria-label="Social network"></span>
      <span class="social-dot" aria-label="Social network"></span>
      <span class="social-dot" aria-label="Social network"></span>
      <span class="rule"></span>
    </div>
  </section>

  <section class="card card--back" aria-label="Card back">
    <div class="back-mark" aria-hidden="true"></div>
    <div class="brand-name">TIDEBLOOM</div>
    <div class="tagline">1 STORY &nbsp;1 PURPOSE</div>
    <h1 class="person-name">MATHILDE T.</h1>
    <p class="person-role">MESSAGE COACH/HEAD STORYTELLER</p>
    <div class="divider"></div>
    <ul class="contact-list">
      <li><svg viewBox="0 0 12 12"><path d="M2.5 0.5l2 2.2-1 1.4c.7 1.6 1.9 2.8 3.5 3.5l1.4-1 2.2 2-1.2 2.2C4.9 10.6 1.4 7.1 0.3 1.7z"/></svg>514-555-0147</li>
      <li><svg viewBox="0 0 12 12"><path d="M3 0h6v12H3zM4 1.5v8h4v-8zM5.5 10.2h1v1h-1z" fill-rule="evenodd"/></svg>514-555-0183.</li>
      <li><svg viewBox="0 0 12 12"><rect x="0" y="2.5" width="12" height="7"/><path d="M0.6 3.1L6 6.7l5.4-3.6" stroke="#f6f6f6" stroke-width="0.9" fill="none"/></svg>mathilde@tidebloom.com</li>
    </ul>
    <p class="website">www.tidebloom.com</p>
  </section>
</body>
</html>
```